Executive Business Card for Healthcare Company [Need Today]

I need a business card design for a healthcare company. The only branding the company has thus far is a logo. The cards will be utilized by company executives. The design I envision will be vibrant and appealing but with a corporate feel. They shouldn't be too casual or playful. I would like to complete this project TODAY if possible.

Target Market(s)

Healthcare vendors, other executives in healthcare and pharmaceuticals

Industry/Entity Type

Pharmaceutical

Contact Information for Business Card

See attachment

Font styles to use
Serif
Sans Serif

Colors

Designer to choose colors to be used in the design.

```html
<!DOCTYPE html>
<html lang="en">
<head>
<meta charset="utf-8">
<title>Corvane Therapeutics – Business Card</title>
<link rel="stylesheet" href="https://fonts.googleapis.com/css2?family=Arimo:wght@400;700&display=swap">
<style>
  :root {
    --teal: #2fbfca;
    --teal-light: #52d6dd;
    --teal-dark: #23a9b6;
    --mint: #9fdfc6;
    --mint-line: #7fd0b1;
    --paper: #ffffff;
    --grey-text: #8a9094;
    --stage: #e9ecec;
  }
  * { margin: 0; padding: 0; box-sizing: border-box; }
  html, body { width: 1200px; height: 780px; overflow: hidden; }
  body {
    background: var(--stage);
    font-family: "Arimo", Arial, sans-serif;
    position: relative;
  }
  .card {
    position: absolute;
    top: 235px;
    width: 540px;
    height: 310px;
    border-radius: 4px;
    overflow: hidden;
    box-shadow: 0 8px 24px rgba(0,0,0,.12);
  }
  .card--front { left: 40px; background: var(--paper); }
  .card--back { left: 620px; }

  /* Front */
  .brand-lockup {
    position: absolute; left: 34px; top: 92px;
    display: flex; align-items: center; gap: 14px;
  }
  .brand-lockup__mark {
    width: 58px; height: 58px; border-radius: 50%;
    border: 3px solid var(--mint-line);
  }
  .brand-lockup__divider { width: 1px; height: 46px; background: #c9cfd1; }
  .brand-lockup__name { color: var(--teal); font-size: 30px; line-height: 1; }
  .brand-lockup__sub { color: var(--grey-text); font-size: 14px; margin-top: 3px; letter-spacing: .5px; }

  .band-strip {
    position: absolute; left: 0; right: 0; top: 186px; height: 30px;
    background: var(--mint);
    display: flex; align-items: center; padding-left: 34px;
    color: var(--paper); font-size: 15px;
  }
  .band-strip__name { font-weight: 700; }
  .band-strip__sep { width: 1px; height: 16px; background: var(--paper); margin: 0 12px; opacity: .8; }
  .band-strip__title { font-size: 13px; }

  .band-main {
    position: absolute; left: 0; right: 0; top: 216px; bottom: 0;
    background: linear-gradient(90deg, var(--teal-dark), var(--teal-light));
    padding: 10px 34px; color: var(--paper); font-size: 12.5px; line-height: 16px;
  }
  .contact-line { display: flex; align-items: center; gap: 7px; }
  .contact-line svg { width: 11px; height: 11px; flex: none; }
  .contact-company { font-weight: 700; }

  .band-circle {
    position: absolute; left: 374px; top: 22px;
    width: 160px; height: 160px; border-radius: 50%;
    background: var(--paper); border: 5px solid var(--mint-line);
  }

  /* Back */
  .back-pattern {
    position: absolute; inset: 0;
    background: radial-gradient(circle at 45% 40%, var(--teal-light), var(--teal) 60%, var(--teal-dark));
  }
  .back-mark {
    position: absolute; left: 50px; top: 205px;
    width: 76px; height: 76px; border-radius: 50%;
    border: 3px solid var(--paper);
    display: flex; align-items: center; justify-content: center;
    color: var(--paper); font-size: 13px;
  }
</style>
</head>
<body>
  <section class="card card--front" aria-label="Business card front">
    <div class="brand-lockup">
      <div class="brand-lockup__mark"></div>
      <div class="brand-lockup__divider"></div>
      <div>
        <div class="brand-lockup__name">corvane</div>
        <div class="brand-lockup__sub">therapeutics</div>
      </div>
    </div>
    <div class="band-circle"></div>
    <div class="band-strip">
      <span class="band-strip__name">Martin Kessler</span>
      <span class="band-strip__sep"></span>
      <span class="band-strip__title">Senior Director of Marketing</span>
    </div>
    <div class="band-main">
      <div class="contact-line">
        <svg viewBox="0 0 12 12"><rect x="1" y="1" width="10" height="10" rx="2" fill="none" stroke="#fff"/><path d="M4 3.5h4v5H4z" fill="#fff"/></svg>
        <span>555-210-4837</span>
      </div>
      <div class="contact-line">
        <svg viewBox="0 0 12 12"><rect x="1" y="1" width="10" height="10" rx="2" fill="none" stroke="#fff"/><path d="M3.5 4.5h5v4h-5zM5 3.5h2v1H5z" fill="#fff"/></svg>
        <span>555-210-6152</span>
      </div>
      <div class="contact-line">
        <svg viewBox="0 0 12 12"><rect x="1" y="1" width="10" height="10" rx="2" fill="none" stroke="#fff"/><path d="M3 4h6v4H3z" fill="none" stroke="#fff" stroke-width=".8"/><path d="M3 4l3 2.2L9 4" fill="none" stroke="#fff" stroke-width=".8"/></svg>
        <span>mkessler@corvanerx.com</span>
      </div>
      <div class="contact-company">Corvane Therapeutics, LLC</div>
      <div>118 W Linden Avenue, Easton, PA 18042</div>
    </div>
  </section>

  <section class="card card--back" aria-label="Business card back">
    <div class="back-pattern" role="img" aria-label="Repeating faint brand-mark pattern in teal tones"></div>
    <div class="back-mark">corvane</div>
  </section>
</body>
</html>
```